indépendant en tant que Massothérapeute et Préparateur Mental, j'ai besoin de ...

Massothérapeute et préparateur mental indépendant, je recherche une carte de visite sobre et dynamique, sans images liées au massage ou à la préparation mentale mais intégrant mon logo. Les couleurs que j'aime bien sont : Blanc, gris, anthracite, noir et jaune

Contact Information for Business Card

carte de préférence Horizontale
neutre qui puisse toucher le deux domaines Massothérapie et préparation mentale

Requirements
Must have
• mon projet doit intégrer au recto:
LOGO
Loïc Bardèze
078 513 26 48
info@loicbardeze.ch
et éventuellement www.loicbardeze.ch

et au verso les deux adresses:

Chemin des Ormilles 7B
1400 Yverdon-les-Bains

Route de la Gravière 9
1700 Fribourg

Should not have
• mon projet ne doit pas contenir d'image en liens avec le massage ni la préparation mentale.

```html
<!DOCTYPE html>
<html lang="fr">
<head>
<meta charset="utf-8">
<title>Loïc Bardèze – Cartes de visite</title>
<link rel="stylesheet" href="https://fonts.googleapis.com/css2?family=Source+Sans+3:wght@400;600&display=swap">
<style>
  :root {
    --backdrop: #e3e3e3;
    --anthracite: #2d2d2d;
    --paper: #f4f4f4;
    --ink: #2a2a2a;
    --white: #ffffff;
  }
  html, body {
    margin: 0;
    padding: 0;
    width: 1200px;
    height: 960px;
    overflow: hidden;
    background: var(--backdrop);
    font-family: "Source Sans 3", "Myriad Pro", Arial, sans-serif;
  }
  .canvas { position: relative; width: 1200px; height: 960px; }
  .card {
    position: absolute;
    left: 323px;
    width: 557px;
    height: 360px;
  }
  .card--front { top: 103px; background: var(--anthracite); color: var(--white); }
  .card--back { top: 495px; background: var(--paper); color: var(--ink); }

  .brand {
    position: absolute;
    left: 62px;
    display: flex;
    align-items: center;
    gap: 16px;
  }
  .card--front .brand { top: 159px; }
  .card--back .brand { top: 53px; }
  .brand__square {
    width: 40px;
    height: 40px;
    background: currentColor;
  }
  .brand__text { display: flex; flex-direction: column; }
  .brand__name {
    font-size: 30px;
    font-weight: 600;
    line-height: 1;
    letter-spacing: 0.5px;
  }
  .brand__role {
    margin-top: 6px;
    font-size: 11px;
    font-weight: 600;
    letter-spacing: 0.6px;
    line-height: 1;
  }

  .contact-name {
    position: absolute;
    left: 62px;
    top: 185px;
    margin: 0;
    font-size: 20px;
    font-weight: 400;
  }
  .contact-rule {
    position: absolute;
    left: 62px;
    top: 227px;
    width: 33px;
    height: 2px;
    background: var(--ink);
  }
  .contact-list {
    position: absolute;
    left: 62px;
    top: 253px;
    margin: 0;
    padding: 0;
    list-style: none;
    font-size: 15px;
    line-height: 20px;
  }
  .contact-list li { display: flex; align-items: center; gap: 7px; }
  .contact-list svg { width: 13px; height: 13px; fill: var(--ink); flex: none; }

  .addresses {
    position: absolute;
    left: 288px;
    top: 214px;
    font-size: 15px;
    line-height: 20px;
    font-style: normal;
  }
  .addresses p { margin: 0 0 18px; }
</style>
</head>
<body>
<div class="canvas">
  <section class="card card--front" aria-label="Recto">
    <div class="brand">
      <span class="brand__square"></span>
      <div class="brand__text">
        <span class="brand__name">Loïc Bardèze</span>
        <span class="brand__role">Massothérapeute / Préparateur Mental</span>
      </div>
    </div>
  </section>

  <section class="card card--back" aria-label="Verso">
    <div class="brand">
      <span class="brand__square"></span>
      <div class="brand__text">
        <span class="brand__name">Loïc Bardèze</span>
        <span class="brand__role">Massothérapeute / Préparateur Mental</span>
      </div>
    </div>

    <h2 class="contact-name">Loïc Bardèze</h2>
    <div class="contact-rule"></div>
    <ul class="contact-list">
      <li>
        <svg viewBox="0 0 24 24" aria-hidden="true"><path d="M6.6 10.8a15.1 15.1 0 0 0 6.6 6.6l2.2-2.2a1 1 0 0 1 1-.25 11.4 11.4 0 0 0 3.6.57 1 1 0 0 1 1 1V20a1 1 0 0 1-1 1A17 17 0 0 1 3 4a1 1 0 0 1 1-1h3.5a1 1 0 0 1 1 1c0 1.25.2 2.45.57 3.6a1 1 0 0 1-.25 1z"/></svg>
        078 513 26 48
      </li>
      <li>
        <svg viewBox="0 0 24 24" aria-hidden="true"><path d="M2 4h20v16H2zm2 2v.5l8 5 8-5V6zm0 2.9V18h16V8.9l-8 5z"/></svg>
        info@loicbardeze.ch
      </li>
      <li>
        <svg viewBox="0 0 24 24" aria-hidden="true"><path d="M12 2a10 10 0 1 0 0 20 10 10 0 0 0 0-20zm6.9 6h-3a15 15 0 0 0-1.3-3.9A8 8 0 0 1 18.9 8zM12 4.1c.8 1.1 1.5 2.4 1.9 3.9h-3.8c.4-1.5 1.1-2.8 1.9-3.9zM4.3 14a8 8 0 0 1 0-4h3.4a16 16 0 0 0 0 4zm.8 2h3a15 15 0 0 0 1.3 3.9A8 8 0 0 1 5.1 16zm3-8h-3a8 8 0 0 1 4.3-3.9A15 15 0 0 0 8.1 8zM12 19.9c-.8-1.1-1.5-2.4-1.9-3.9h3.8c-.4 1.5-1.1 2.8-1.9 3.9zm2.3-5.9H9.7a14 14 0 0 1 0-4h4.6a14 14 0 0 1 0 4zm.3 5.9a15 15 0 0 0 1.3-3.9h3a8 8 0 0 1-4.3 3.9zm1.7-5.9a16 16 0 0 0 0-4h3.4a8 8 0 0 1 0 4z"/></svg>
        www.loicbardeze.ch
      </li>
    </ul>

    <address class="addresses">
      <p>Chemin des Ormilles 7B<br>1400 Yverdon-les-Bains</p>
      <p>Route de la Gravière 9<br>1700 Fribourg</p>
    </address>
  </section>
</div>
</body>
</html>
```